Clear Plastic Card Design

I am looking to have a business card designed from my logo icon. I am looking to match the style of a different business card I have attached in the files.
Looking for a card that is plastic, with layers of transparency in the shape of my logo icon (also attached in the files) - not a circle like the other card. The winning design will incorporate the red icon logo on the front and back and include the charity's name, "Light for the Weary Souls" in the same or similar font, as well as an email and phone number. For now, use the email: email@lightfortheweary-mail.org and the phone number 555-382-7194.
We like how the sample business card has transparency, partial and full opacity layers and a matching color scheme. Files will need to be in vector so that our business card printing company can work with it.
UPDATE:
We've some excellent designs in, thank you everyone! I got an early review from the owner, and he requested a minor redirect to find his perfect design. He wants the design to stand out by NOT being a rectangle. Try instead a circle, square, or best yet - something that falls in the outline of the logo icon, either fully or partially. Thank you, everyone!
Light for the Weary Souls text should be incorporated as well as a phone and email.

```html
<!DOCTYPE html>
<html lang="en">
<head>
<meta charset="utf-8">
<title>Light for the Weary Souls – Business Card</title>
<link href="https://fonts.googleapis.com/css2?family=Montserrat:wght@400;500;700&display=swap" rel="stylesheet">
<style>
  :root {
    --page-bg: #e6eaee;
    --clear-top: #eef3f6;
    --clear-bottom: #dfe7ec;
    --card-edge: #ffffff;
    --ink: #141414;
    --brand-red: #c41d2f;
    --brand-orange: #d2571c;
    --band-edge: #1b1b1f;
    --light-text: #f3ece8;
    --icon-fill: #f1d9cf;
  }
  * { margin: 0; padding: 0; box-sizing: border-box; }
  html, body { width: 1200px; height: 1008px; overflow: hidden; }
  body {
    background: var(--page-bg);
    font-family: "Montserrat", sans-serif;
    position: relative;
  }
  .card {
    position: absolute;
    left: 290px;
    top: 194px;
    width: 620px;
    height: 620px;
    border-radius: 44px;
    border: 2px solid var(--card-edge);
    overflow: hidden;
    background: linear-gradient(170deg, var(--clear-top), var(--clear-bottom));
    box-shadow: 0 18px 40px rgba(40, 55, 70, 0.18);
  }
  .contact-band {
    position: absolute;
    left: 0; top: 0;
    width: 620px; height: 620px;
  }
  .brand {
    position: absolute;
    left: 112px;
    top: 112px;
    display: flex;
    align-items: center;
    gap: 22px;
  }
  .brand-square {
    width: 112px; height: 112px;
    background: linear-gradient(135deg, var(--brand-red), var(--brand-orange));
    border-radius: 6px;
  }
  .brand-name {
    font-weight: 500;
    font-size: 36px;
    line-height: 1.15;
    color: var(--ink);
    letter-spacing: -0.3px;
  }
  .details {
    position: absolute;
    left: 0; right: 0;
    top: 388px;
    text-align: center;
    color: var(--light-text);
  }
  .person-name {
    font-weight: 700;
    font-size: 32px;
    letter-spacing: 0.5px;
  }
  .divider {
    display: flex;
    align-items: center;
    justify-content: center;
    gap: 8px;
    margin-top: 20px;
  }
  .divider-line { width: 110px; height: 2px; background: var(--light-text); }
  .divider-icon {
    width: 30px; height: 30px;
    border-radius: 50%;
    background: var(--icon-fill);
    display: flex; align-items: center; justify-content: center;
  }
  .phone { font-size: 22px; margin-top: 20px; }
  .email { font-size: 21px; margin-top: 14px; }
</style>
</head>
<body>
  <div class="card">
    <svg class="contact-band" viewBox="0 0 620 620" aria-hidden="true">
      <defs>
        <linearGradient id="bandFill" x1="0" y1="0" x2="1" y2="0.3">
          <stop offset="0" stop-color="#c41d2f"/>
          <stop offset="0.5" stop-color="#c03a26"/>
          <stop offset="1" stop-color="#d2571c"/>
        </linearGradient>
      </defs>
      <path d="M0 336 Q310 290 620 336 L620 620 L0 620 Z" fill="var(--band-edge)"/>
      <path d="M0 348 Q310 292 620 348 L620 620 L0 620 Z" fill="url(#bandFill)"/>
    </svg>

    <div class="brand">
      <div class="brand-square"></div>
      <div class="brand-name">Light for the<br>Weary Souls</div>
    </div>

    <div class="details">
      <div class="person-name">DANIEL HARWICK</div>
      <div class="divider">
        <span class="divider-line"></span>
        <span class="divider-icon">
          <svg width="16" height="16" viewBox="0 0 24 24" aria-label="Phone">
            <path fill="#c23a28" d="M6.6 10.8a15.1 15.1 0 0 0 6.6 6.6l2.2-2.2a1 1 0 0 1 1-.25 11.4 11.4 0 0 0 3.6.57 1 1 0 0 1 1 1V20a1 1 0 0 1-1 1A17 17 0 0 1 3 4a1 1 0 0 1 1-1h3.5a1 1 0 0 1 1 1c0 1.25.2 2.45.57 3.57a1 1 0 0 1-.25 1z"/>
          </svg>
        </span>
        <span class="divider-icon">
          <svg width="16" height="16" viewBox="0 0 24 24" aria-label="Email">
            <rect x="2" y="5" width="20" height="14" rx="1.5" fill="none" stroke="#c23a28" stroke-width="2"/>
            <path d="M3 6l9 7 9-7" fill="none" stroke="#c23a28" stroke-width="2"/>
          </svg>
        </span>
        <span class="divider-line"></span>
      </div>
      <div class="phone">555-382-7194</div>
      <div class="email">email@lightfortheweary-mail.org</div>
    </div>
  </div>
</body>
</html>
```